QVR business card

Need a business card for a company that provides instructional design and elearning development services. The website is here: http://quorvane.studio/

I'm attaching a current logo, as well as the old business card design. While I like to keep it clean, the old design is too simplistic for my liking. The only idea I want to reuse from the old design is placing industry jargon on the back of the card, just need a better way to present it. But if you have other ideas for the back--feel free to experiment.

Please use the colors complementary to the color we have on the website. Thank you!

```html
<!DOCTYPE html>
<html lang="en">
<head>
<meta charset="utf-8">
<title>QVR business card</title>
<link rel="stylesheet" href="https://fonts.googleapis.com/css2?family=Open+Sans:wdth,wght@75..100,300..800&display=swap">
<style>
  :root {
    --teal: #1fb3b1;
    --teal-dark: #17a3a1;
    --teal-faint: #dcefef;
    --white: #ffffff;
    --ink: #2b2b2b;
    --backdrop: #eceae6;
  }
  * { box-sizing: border-box; margin: 0; padding: 0; }
  html, body {
    width: 1200px; height: 900px; overflow: hidden;
    background: var(--backdrop);
    font-family: "Open Sans", Arial, sans-serif;
  }
  .canvas {
    position: relative; width: 1200px; height: 900px;
  }
  .card {
    position: absolute; left: 250px; width: 700px; height: 400px;
    overflow: hidden;
    box-shadow: 0 6px 18px rgba(0,0,0,0.18);
  }

  /* Back of card */
  .card-back { top: 33px; background: var(--teal); color: var(--white); }
  .help-heading {
    position: absolute; left: 38px; top: 34px;
    font-weight: 800; text-transform: uppercase;
    line-height: 0.92; letter-spacing: 1px;
  }
  .help-heading span { display: block; font-size: 78px; }
  .help-heading .help-we { font-size: 112px; }
  .divider {
    position: absolute; left: 312px; top: 40px; width: 2px; height: 320px;
    background: rgba(255,255,255,0.75);
  }
  .jargon-list {
    position: absolute; left: 336px; top: 44px;
    list-style: none; text-transform: uppercase; white-space: nowrap;
    font-weight: 500; font-stretch: 75%;
    font-size: 30px; line-height: 52px; letter-spacing: 0.5px;
  }

  /* Front of card */
  .card-front { top: 467px; background: var(--white); color: var(--ink); }
  .brand {
    position: absolute; right: 44px; top: 44px;
    display: flex; align-items: center; gap: 12px;
  }
  .brand-mark { width: 26px; height: 26px; background: var(--teal); }
  .brand-name { font-size: 34px; font-weight: 600; color: var(--teal-dark); }
  .brand-accent {
    position: absolute; right: -90px; bottom: -130px;
    width: 330px; height: 330px; border-radius: 50%;
    background: var(--teal-faint);
  }
  .contact-block { position: absolute; left: 40px; top: 218px; }
  .person-name {
    font-size: 21px; font-weight: 700; color: var(--teal-dark);
    text-transform: uppercase; letter-spacing: 0.5px;
  }
  .person-role { font-size: 18px; margin-top: 2px; }
  .contact-list { list-style: none; margin-top: 22px; font-size: 20px; line-height: 31px; }
  .contact-list li { display: flex; align-items: center; gap: 10px; }
  .contact-list svg { width: 18px; height: 18px; fill: var(--teal); flex: none; }
</style>
</head>
<body>
<div class="canvas">

  <section class="card card-back" aria-label="Card back">
    <h2 class="help-heading">
      <span>How</span>
      <span>Can</span>
      <span class="help-we">We</span>
      <span>Help?</span>
    </h2>
    <div class="divider"></div>
    <ul class="jargon-list">
      <li>Mobile Learning SCORM</li>
      <li>Instructional Design LMS</li>
      <li>MOOCs eLearning HTML5</li>
      <li>Adult Learning Theory</li>
      <li>Gamification Classroom</li>
      <li>xAPI Blended Learning</li>
    </ul>
  </section>

  <section class="card card-front" aria-label="Card front">
    <div class="brand-accent"></div>
    <div class="brand">
      <div class="brand-mark"></div>
      <div class="brand-name">Quorvane Studio</div>
    </div>
    <div class="contact-block">
      <p class="person-name">Marcus Delaney</p>
      <p class="person-role">Managing Director</p>
      <ul class="contact-list">
        <li>
          <svg viewBox="0 0 24 24" aria-hidden="true"><path d="M6.6 10.8a15 15 0 0 0 6.6 6.6l2.2-2.2a1 1 0 0 1 1-.25 11.4 11.4 0 0 0 3.6.57 1 1 0 0 1 1 1V20a1 1 0 0 1-1 1A17 17 0 0 1 3 4a1 1 0 0 1 1-1h3.5a1 1 0 0 1 1 1c0 1.250.2 2.450.57 3.57a1 1 0 0 1-.25 1z"/></svg>
          555-013-2748
        </li>
        <li>
          <svg viewBox="0 0 24 24" aria-hidden="true"><path d="M2 5h20v14H2z M3.5 6.5 12 13l8.5-6.5" stroke="#fff" stroke-width="1.5"/></svg>
          mdelaney@quorvane.studio
        </li>
        <li>
          <svg viewBox="0 0 24 24" aria-hidden="true"><circle cx="12" cy="12" r="10"/><path d="M2 12h20M12 2c3 3 3 17 0 20M12 2c-3 3-3 17 0 20M4 7h16M4 17h16" stroke="#fff" stroke-width="1.2" fill="none"/></svg>
          www.quorvane.studio
        </li>
      </ul>
    </div>
  </section>

</div>
</body>
</html>
```